Onboarding Infographic/brochure

We are a small criminal defense firm looking to create some sort of infographic or brochure that we can onboard new clients with. We are currently sending it out via email but want something a bit cooler and fun to send to clients. The information is:

A Few Quick Rules

We are here to help each step of the way. While questions are never discouraged, this letter will answer some of the most common ones we get asked.

Communications

As a client, you should always be in the loop. While we will try to respond to questions as quickly as possible, sometimes we are unable to respond right away. Do not worry - we promise to get back to you soon. Some questions might take some time to research, and a correct answer is better than a quick one.

Appointments

One of the benefits of having an attorney is the ability to discuss your case outside of court, minus the stress and headaches. If you need an appointment, please contact the office.

Appointments must be scheduled in advance. We do not want you to make a special trip to the office only to learn that we are in court or otherwise unavailable.

Jail Visits

If your family member is currently in jail, we take that very seriously. We will visit your loved one and introduce ourselves. While the case is ongoing, we ask that a family member be designated a “contact” person so that messages can be relayed quickly. Never discuss the facts of the case over the phone with someone who is in jail. Jail calls are recorded and we have seen too many cases go south based on remarks made over recorded lines.

Police Reports and Discovery

We will do our best to provide you with copies of everything we receive on your case. Most information will be emailed, so please keep your email address up to date.

Changes in Contact Information

If you move or change numbers during the case, please let us know. It is difficult to help if we are unable to reach you, and helping you is why we are here.

Court Appearances

Cases do not get resolved as quickly as they do on television. Expect there to be several hearings in your case and it may be necessary for you to attend one or more of them. If a hearing is set, you will receive notice of the date and time of each hearing.

Billing and Collections

We understand that this investment was a huge decision for you. As we focus on providing the best representation, we will need for you to stay on schedule with any payment arrangements agreed to at the time of your initial consultation.

Again, thank you for your trust in us. We look forward to getting a fantastic outcome on your case.

Target Market(s)

Criminal defense clients and their families

Industry/Entity Type

Legal

Font styles to use
Serif

Requirements
Must have
• Must incorporate all of the rules we email out. Would like diagrams, images or pictures
Nice to have
• We attached a Welcome brochure. Not sure I want it to look super similar, hence the request for infographic.

```html
<!DOCTYPE html>
<html lang="en">
<head>
<meta charset="utf-8">
<title>Northgate Legal Group – A Few Quick Rules</title>
<link href="https://fonts.googleapis.com/css2?family=Montserrat:wght@400;500;700;800;900&family=Great+Vibes&display=swap" rel="stylesheet">
<style>
:root{
  --navy:#17232e;
  --navy-2:#1d3856;
  --sky:#8aaedd;
  --royal:#0a47b0;
  --grey:#dcdcdc;
  --grey-card:#e0e0e0;
  --ink:#1f2328;
  --white:#ffffff;
}
*{margin:0;padding:0;box-sizing:border-box}
html,body{width:1200px;height:2262px;overflow:hidden;background:#fff}
body{font-family:"Montserrat",sans-serif;color:var(--ink);position:relative}
.abs{position:absolute}
.fill{border-radius:6px}

/* header */
.hero{left:0;top:0;width:1200px;height:555px;background:linear-gradient(135deg,var(--navy) 40%,var(--navy-2));overflow:hidden}
.hero-stripe{right:0;top:0}
.brand{left:81px;top:82px;color:var(--white)}
.brand-name{font-weight:900;font-size:48px;letter-spacing:-1px;line-height:1}
.brand-sub{font-weight:700;font-size:14px;letter-spacing:11px;margin-top:2px}
.kicker{left:81px;top:186px;color:var(--white);font-weight:500;font-size:44px;letter-spacing:14px}
.title-quick{left:78px;top:236px;color:var(--sky);font-weight:900;font-size:96px;line-height:1;letter-spacing:-2px}
.title-rules{left:78px;top:330px;color:var(--white);font-weight:900;font-size:96px;line-height:1;letter-spacing:-2px}
.intro{left:81px;top:444px;width:330px;color:var(--white);font-size:14.5px;line-height:18.5px}
.intro b{font-weight:700}
.hero-art{left:477px;top:79px;width:513px;height:435px;border-radius:10px;background:radial-gradient(ellipse at 50% 55%,#eceef0 0%,#c9ced4 55%,rgba(201,206,212,0) 75%)}

/* shared */
.tab{width:88px;height:44px;border-radius:0 0 44px 44px;color:var(--white);font-weight:800;font-size:19px;display:flex;align-items:center;justify-content:center}
.tab.blue{background:var(--royal)}
.tab.dark{background:var(--navy)}
.h{color:var(--royal);font-weight:800;font-size:20px;letter-spacing:3.5px;line-height:23px;text-transform:uppercase}
.p{font-size:14.5px;line-height:18.5px;color:var(--ink)}

/* row 1 */
.band-1{left:0;top:574px;width:1200px;height:342px;background:var(--grey)}
.band-1 .split{left:589px;top:0;width:8px;height:342px;background:#eaeaea}
.tab-1{left:79px;top:574px}
.tab-2{left:595px;top:574px}
.art-people{left:72px;top:635px;width:200px;height:244px;background:linear-gradient(180deg,#c9ced2,#8e9499)}
.comm-title{left:290px;top:598px}
.comm-text{left:290px;top:634px;width:235px}
.comm-text b{display:block;margin-top:8px;font-weight:800}
.art-scales-1{left:639px;top:595px;width:167px;height:147px;background:linear-gradient(180deg,#e8c774,#b98a2e)}
.appt-title{left:857px;top:598px}
.appt-text{left:857px;top:634px;width:262px}
.appt-note{left:635px;top:787px;width:480px;height:113px;background:var(--royal);border-radius:12px;color:var(--white);font-size:14.5px;line-height:18.5px;padding:10px 170px 0 19px}
.art-clip-1{left:974px;top:760px;width:103px;height:124px;background:linear-gradient(180deg,#dfe8fb,#7fa2e6)}

/* jail */
.jail{left:0;top:937px;width:1200px;height:186px;background:var(--navy)}
.art-cell{left:0;top:937px;width:378px;height:186px;background:radial-gradient(ellipse at 50% 45%,#5d5f61,#1f2021)}
.tab-3{left:415px;top:937px}
.jail-title{left:526px;top:962px;color:var(--sky)}
.jail-text{left:414px;top:998px;width:715px;color:var(--white);font-size:14.5px;line-height:18.5px}

/* cards */
.card{top:1149px;width:331px;height:413px;background:var(--grey-card);border-radius:40px 0 40px 0;overflow:hidden}
.card-4{left:80px}
.card-mid{left:433px;background:var(--royal)}
.card-5{left:785px}
.corner{position:absolute;right:0;top:0;width:62px;height:62px;border-radius:0 0 0 62px;color:var(--white);font-weight:800;font-size:19px;display:flex;align-items:center;justify-content:center;padding:0 0 6px 8px}
.corner.blue{background:var(--royal)}
.corner.dark{background:var(--navy)}
.art-report{left:0;top:22px;width:182px;height:160px;background:linear-gradient(135deg,#f2c6a6,#3f6fd8)}
.art-justice{left:66px;top:48px;width:221px;height:328px;background:linear-gradient(180deg,#e5c16a 0%,#c99a3c 45%,#8e2b2b 75%,#e9e9e9 100%);opacity:.9}
.art-badge{left:0;top:20px;width:190px;height:165px;background:linear-gradient(135deg,#6e7378,#f2c26b)}
.card .h{position:absolute;left:27px;width:290px}
.card .p{position:absolute;left:27px;width:278px}
.card-4 .h{top:212px}
.card-4 .p{top:270px}
.card-5 .h{top:209px}
.card-5 .p{top:284px}

/* row 3 */
.split-2{left:591px;top:1562px;width:8px;height:328px;background:#f0f0f0}
.tab-6{left:86px;top:1562px}
.tab-7{left:610px;top:1562px}
.art-court{left:38px;top:1640px;width:272px;height:224px;background:linear-gradient(180deg,#f4ede4,#cbb9a2)}
.court-title{left:328px;top:1626px}
.court-text{left:328px;top:1686px;width:235px}
.bill-title{left:627px;top:1626px}
.bill-text{left:627px;top:1686px;width:258px}
.art-gavel{left:902px;top:1625px;width:207px;height:244px;background:linear-gradient(160deg,#dfe6f7,#f0a238 60%,#8d5a34)}

/* footer */
.footer{left:0;top:1890px;width:1200px;height:372px;background:var(--navy)}
.thanks{left:0;top:1924px;width:1200px;text-align:center;font-family:"Great Vibes",cursive;font-size:50px;color:var(--sky)}
.thanks-line{left:0;top:1990px;width:1200px;text-align:center;color:var(--white);font-weight:700;font-size:23px;line-height:30px}
.pill{top:2077px;width:337px;height:49px;border-radius:8px;background:var(--sky);display:flex;overflow:hidden}
.pill-label{width:97px;background:var(--royal);color:var(--white);font-weight:800;font-size:17px;line-height:17px;display:flex;align-items:center;justify-content:center;text-align:left}
.pill-num{flex:1;display:flex;align-items:center;justify-content:center;gap:8px;font-weight:700;font-size:24px;color:var(--navy)}
.pill-1{left:81px}
.pill-2{left:430px}
.pill-3{left:778px}
.web{left:0;top:2152px;width:1200px;text-align:center;color:var(--white);font-size:22px;letter-spacing:7px}
.web b{font-weight:800}
</style>
</head>
<body>

<section class="abs hero">
  <svg class="abs hero-stripe" width="420" height="555" viewBox="0 0 420 555" aria-hidden="true">
    <polygon points="352,0 420,0 420,555 130,555" fill="#8aaedd"/>
    <polygon points="370,165 420,270 420,555 330,555" fill="#ffffff"/>
  </svg>
  <div class="abs brand"><div class="brand-name">NORTHGATE</div><div class="brand-sub">LEGAL GROUP</div></div>
  <div class="abs kicker">A FEW</div>
  <div class="abs title-quick">QUICK</div>
  <div class="abs title-rules">RULES</div>
  <p class="abs intro">We are here to <b>help each step of the way</b>. While questions are never discouraged, this letter will answer some of the most common ones we get asked</p>
</section>
<div class="abs hero-art" role="img" aria-label="3D illustration of a white courthouse with columns and a flag"></div>

<section class="abs band-1"><div class="abs split"></div></section>
<div class="abs tab blue tab-1">1</div>
<div class="abs tab dark tab-2">2</div>
<div class="abs fill art-people" role="img" aria-label="3D illustration of two business people shaking hands with speech bubbles"></div>
<h2 class="abs h comm-title">Communications</h2>
<div class="abs p comm-text">As a client, you should always be in the loop. While we will try to respond to questions as quickly as possible, sometimes we are unable to respond right away
  <b>Do not worry - we promise to get back to you soon. Some questions might take some time to research, and a correct answer is better than a quick one</b></div>
<div class="abs fill art-scales-1" role="img" aria-label="Golden scales of justice"></div>
<h2 class="abs h appt-title">Appointments</h2>
<p class="abs p appt-text">One of the benefits of having an attorney is the ability to discuss your case outside of court, minus the stress and headaches. If you need an appointment, please contact the office</p>
<p class="abs appt-note">Appointments must be scheduled in advance. We do not want you to make a special trip to the office only to learn that we are in court or otherwise unavailable</p>
<div class="abs fill art-clip-1" role="img" aria-label="Clipboard checklist with alarm bell"></div>

<section class="abs jail"></section>
<div class="abs art-cell" role="img" aria-label="Dark empty jail cell with barred windows"></div>
<div class="abs tab blue tab-3">3</div>
<h2 class="abs h jail-title">Jail Visits</h2>
<p class="abs jail-text">If your family member is currently in jail, we take that very seriously. We will visit your loved one and introduce ourselves. While the case is ongoing, we ask that a family member be designated a “contact” person so that messages can be relayed quickly. Never discuss the facts of the case over the phone with someone who is in jail. Jail calls are recorded and we have seen too many cases go south based on remarks made over recorded lines</p>

<article class="abs card card-4">
  <div class="abs fill art-report" role="img" aria-label="Hand holding a checklist report"></div>
  <div class="corner dark">4</div>
  <h2 class="h">Police Reports<br>and Discovery</h2>
  <p class="p">We will do our best to provide you with copies of everything we receive on your case. Most information will be emailed, so please keep your email address up to date</p>
</article>
<article class="abs card card-mid">
  <div class="abs fill art-justice" role="img" aria-label="Golden scales of justice standing on a stack of law books"></div>
</article>
<article class="abs card card-5">
  <div class="abs fill art-badge" role="img" aria-label="Hand holding a phone with a gold badge"></div>
  <div class="corner blue">5</div>
  <h2 class="h">Changes in<br>Contact<br>Information</h2>
  <p class="p">If you move or change numbers during the case, please let us know. It is difficult to help if we are unable to reach you, and helping you is why we are here</p>
</article>

<div class="abs split-2"></div>
<div class="abs tab blue tab-6">6</div>
<div class="abs tab dark tab-7">7</div>
<div class="abs fill art-court" role="img" aria-label="Classical columned courthouse facade"></div>
<h2 class="abs h court-title">Court<br>Appearances</h2>
<p class="abs p court-text">Cases do not get resolved as quickly as they do on television. Expect there to be several hearings in your case and it may be necessary for you to attend one or more of them. If a hearing is set, you will receive notice of the date and time of each hearing</p>
<h2 class="abs h bill-title">Billing and<br>Collections</h2>
<p class="abs p bill-text">We understand that this investment was a huge decision for you. As we focus on providing the best representation, we will need for you to stay on schedule with any payment arrangements agreed to at the time of your initial consultation</p>
<div class="abs fill art-gavel" role="img" aria-label="Clipboard checklist with a gavel and clock"></div>

<footer class="abs footer"></footer>
<div class="abs thanks">Again, thank you</div>
<p class="abs thanks-line">For your trust in us. We look forward to getting a fantastic<br>outcome on your case</p>

<div class="abs pill pill-1"><div class="pill-label">TOLL<br>FREE</div><div class="pill-num"><svg width="20" height="20" viewBox="0 0 20 20" aria-hidden="true"><circle cx="10" cy="10" r="9" fill="none" stroke="#0a47b0" stroke-width="2"/><path d="M7 5.5l1.6 2.3-1 1.2a6 6 0 0 0 3.4 3.4l1.2-1 2.3 1.6-.8 1.6c-4-.3-7.3-3.6-7.6-7.6z" fill="#0a47b0"/></svg>(888) 555-0142</div></div>
<div class="abs pill pill-2"><div class="pill-label">LA<br>AREA</div><div class="pill-num"><svg width="20" height="20" viewBox="0 0 20 20" aria-hidden="true"><circle cx="10" cy="10" r="9" fill="none" stroke="#0a47b0" stroke-width="2"/><path d="M7 5.5l1.6 2.3-1 1.2a6 6 0 0 0 3.4 3.4l1.2-1 2.3 1.6-.8 1.6c-4-.3-7.3-3.6-7.6-7.6z" fill="#0a47b0"/></svg>(213) 555-0187</div></div>
<div class="abs pill pill-3"><div class="pill-label">INLAND</div><div class="pill-num"><svg width="20" height="20" viewBox="0 0 20 20" aria-hidden="true"><circle cx="10" cy="10" r="9" fill="none" stroke="#0a47b0" stroke-width="2"/><path d="M7 5.5l1.6 2.3-1 1.2a6 6 0 0 0 3.4 3.4l1.2-1 2.3 1.6-.8 1.6c-4-.3-7.3-3.6-7.6-7.6z" fill="#0a47b0"/></svg>(909) 555-0163</div></div>

<div class="abs web">www.<b>northgatelegalgroup</b>.com</div>

</body>
</html>
```